Executive Taxi firm with Chauffeur service Website

I have my domain name registered and I have started to work on my site but I am struggling. I am just about to get a logo for the company and need a web site that clearly represents the fact we are an executive/luxury brand in private hire vehicles. We offer airport transfers, train station transfers, seaport transfers, holiday transfers and business to business pick up and drop off.

Target Market(s)

Corporate people, holidaymakers looking for a luxury start their holiday. VIPs' and celebrities.

Number of Pages Required

5+ page

Font styles to use
Serif
Sans Serif
Decorative
Script

Colors

Designer to choose colors to be used in the design.

Requirements
Must have
• Home Page, Services, About Us, VIP and Contact us
• Please see www.brivomotors.co.uk I have started it but not happy with it at all.
Nice to have
• Booking form or enquiry form.

```html
<!DOCTYPE html>
<html lang="en">
<head>
<meta charset="utf-8">
<title>Crestway Travel — Executive Road Travel</title>
<link rel="stylesheet" href="https://fonts.googleapis.com/css2?family=Montserrat:wght@500;600;700;800&family=Roboto:wght@300;400;500&display=swap">
<style>
:root{
  --orange:#e2561f;
  --orange-deep:#c8431a;
  --orange-soft:#f08a4e;
  --ink:#2b2b2b;
  --text:#4a4a4a;
  --white:#ffffff;
  --field:#ffffff;
}
*{box-sizing:border-box;margin:0;padding:0}
html,body{width:1200px;height:3509px;overflow:hidden}
body{font-family:"Roboto",sans-serif;color:var(--text);background:var(--white);position:relative}
section,header,footer{position:absolute;left:0;width:1200px}
h2{font-family:"Montserrat",sans-serif;font-weight:800;text-transform:uppercase}
a{text-decoration:none}

/* Header */
.site-header{top:0;height:102px;background:var(--white);z-index:3}
.brand{position:absolute;left:112px;top:28px;display:flex;align-items:center;gap:12px}
.brand-dot{width:40px;height:40px;border-radius:50%;background:var(--orange)}
.brand-name{font-family:"Montserrat",sans-serif;font-weight:800;font-size:28px;color:var(--orange);text-transform:uppercase;letter-spacing:.5px}
.main-nav{position:absolute;right:112px;top:40px;display:flex;gap:46px}
.main-nav a{font-family:"Roboto",sans-serif;font-size:17px;color:var(--ink);text-transform:uppercase;position:relative}
.main-nav a.active{color:var(--orange)}
.main-nav a.active::after{content:"";position:absolute;left:0;right:0;bottom:-9px;height:2px;background:var(--orange)}

/* Hero */
.hero{top:102px;height:640px;overflow:hidden}
.hero-photo{position:absolute;inset:0;background:linear-gradient(100deg,#8a2f10 0%,#c4501f 30%,#e07a45 55%,#b9461c 80%,#8f3514 100%)}
.hero-title{position:absolute;top:190px;width:100%;text-align:center;font-family:"Montserrat",sans-serif;font-weight:800;font-size:62px;color:var(--white);text-transform:uppercase}
.hero-sub{position:absolute;top:268px;width:100%;text-align:center;font-size:26px;font-weight:300;color:var(--white)}
.btn{display:inline-block;background:var(--orange);color:var(--white);font-family:"Montserrat",sans-serif;font-weight:700;text-transform:uppercase;border-radius:30px;text-align:center;text-decoration:none}
.hero-btn{position:absolute;left:482px;top:326px;width:238px;height:54px;line-height:54px;font-size:19px}
.hero-arrow{position:absolute;top:250px}
.hero-wave{position:absolute;left:0;bottom:0}

/* Welcome */
.welcome{top:742px;height:570px;text-align:center}
.welcome h2{margin-top:56px;font-size:34px;color:var(--ink)}
.welcome h2 span,.always h2 span{color:var(--orange)}
.welcome .lead{width:680px;margin:24px auto 0;font-size:15px;line-height:25px;color:var(--ink)}
.services{position:absolute;top:208px;left:106px;display:flex;gap:0}
.service{width:205px;text-align:center}
.service-icon{width:134px;height:134px;margin:0 auto;border-radius:50%;background:var(--orange);border:4px solid #f7c7ae;box-shadow:0 0 0 3px var(--orange);display:flex;align-items:center;justify-content:center}
.service h3{margin:30px auto 0;width:150px;font-family:"Montserrat",sans-serif;font-weight:600;font-size:17px;color:var(--orange);line-height:20px;min-height:40px}
.service p{margin:6px auto 0;width:160px;font-size:13px;line-height:21px;color:var(--ink)}

/* About */
.about{top:1312px;height:536px;overflow:hidden}
.about-photo{position:absolute;inset:0;background:linear-gradient(120deg,#e06a35 0%,#ef8a55 40%,#d2582a 75%,#a93f18 100%)}
.about h2{position:absolute;top:60px;width:100%;text-align:center;color:var(--white);font-size:34px}
.about-card{position:absolute;left:145px;top:131px;width:910px;height:337px;background:rgba(255,255,255,.86);text-align:center;padding:36px 42px 0}
.about-card h3{font-family:"Montserrat",sans-serif;font-weight:500;font-size:21px;color:var(--orange)}
.about-card p{margin-top:28px;font-size:13px;line-height:25px;color:var(--ink)}
.about-card p+p{margin-top:20px}

/* Always here */
.always{top:1848px;height:630px}
.always h2{position:absolute;left:112px;top:88px;font-size:34px;color:var(--ink)}
.always .copy{position:absolute;left:112px;top:150px;width:470px;font-size:13.5px;line-height:25px;color:var(--ink)}
.always .copy p+p{margin-top:17px}
.always-btn{position:absolute;left:112px;top:485px;width:146px;height:40px;line-height:40px;font-size:12px;font-weight:700}
.app-ring{position:absolute;left:670px;top:86px;width:400px;height:400px;border-radius:50%;background:var(--white);box-shadow:0 6px 24px rgba(0,0,0,.15)}
.app-photo{position:absolute;left:16px;top:16px;width:368px;height:368px;border-radius:50%;background:radial-gradient(circle at 45% 40%,#ffd77a 0%,#f4ac3c 45%,#e57b2c 100%)}

/* Booking */
.booking{top:2478px;height:680px;overflow:hidden}
.booking-photo{position:absolute;inset:0;background:linear-gradient(160deg,#d4602d 0%,#ea8250 45%,#d8642f 80%,#c14a1c 100%)}
.booking h2{position:absolute;top:80px;width:100%;text-align:center;color:var(--white);font-size:34px}
.booking-form{position:absolute;left:112px;top:168px;width:976px;display:grid;grid-template-columns:repeat(3,320px);gap:22px 8px}
.field{height:40px;background:var(--field);font-size:14px;color:var(--ink);padding:0 18px;display:flex;align-items:center;justify-content:space-between}
.booking-btn{position:absolute;left:488px;top:306px;width:224px;height:56px;line-height:56px;font-size:19px;background:var(--orange-deep)}
.booking-wave{position:absolute;left:0;bottom:0}

/* Footer */
.site-footer{top:3058px;height:451px;background:var(--orange);color:var(--white)}
.footer-col{position:absolute;top:48px}
.footer-col h4{font-family:"Montserrat",sans-serif;font-weight:700;font-size:16px;text-transform:uppercase}
.footer-col h4::after{content:"";display:block;width:50px;height:2px;background:rgba(255,255,255,.6);margin-top:10px}
.contact-list{margin-top:28px;list-style:none;font-size:13px;line-height:22px}
.contact-list li{display:flex;gap:18px;margin-bottom:20px}
.contact-list svg{flex:none;margin-top:2px}
.link-list{margin-top:26px;list-style:none;font-size:13.5px}
.link-list li{margin-bottom:19px;padding-left:22px;position:relative}
.link-list li::before{content:"";position:absolute;left:2px;top:4px;border-left:6px solid var(--white);border-top:4px solid transparent;border-bottom:4px solid transparent}
.newsletter p{margin-top:28px;font-size:14px}
.email-field{margin-top:26px;width:286px;height:44px;border-radius:22px;background:var(--white);color:var(--text);font-size:13px;padding:0 24px;line-height:44px}
.subscribe{margin-top:10px;width:124px;height:40px;line-height:40px;font-size:13px;background:var(--orange-soft)}
.footer-bottom{position:absolute;left:112px;right:112px;top:352px;border-top:1px solid rgba(255,255,255,.35)}
.copyright{position:absolute;left:0;top:38px;font-size:13px}
.socials{position:absolute;right:30px;top:24px;display:flex;gap:12px}
.socials span{width:32px;height:32px;border-radius:50%;border:1px solid rgba(255,255,255,.8)}
</style>
</head>
<body>

<header class="site-header">
  <div class="brand"><span class="brand-dot"></span><span class="brand-name">Crestway Travel</span></div>
  <nav class="main-nav">
    <a href="#" class="active">Home</a><a href="#">Services</a><a href="#">About Us</a><a href="#">VIP</a><a href="#">Contact Us</a>
  </nav>
</header>

<section class="hero">
  <div class="hero-photo" role="img" aria-label="Photo of a chauffeur-driven executive beside a luxury car and private jet, orange tinted"></div>
  <svg class="hero-arrow" style="left:40px" width="20" height="34" viewBox="0 0 20 34"><path d="M17 2 3 17l14 15" fill="none" stroke="#fff" stroke-opacity=".6" stroke-width="3"/></svg>
  <svg class="hero-arrow" style="right:40px" width="20" height="34" viewBox="0 0 20 34"><path d="M3 2l14 15L3 32" fill="none" stroke="#fff" stroke-opacity=".6" stroke-width="3"/></svg>
  <h1 class="hero-title">Executive Road Travel</h1>
  <p class="hero-sub">Private Hire, Chauffeur and taxi service</p>
  <a class="btn hero-btn" href="#">Book Now</a>
  <svg class="hero-wave" width="1200" height="90" viewBox="0 0 1200 90" preserveAspectRatio="none">
    <path d="M0 40 Q600 120 1200 0 V90 H0Z" fill="var(--orange)"/>
    <path d="M0 58 Q600 130 1200 20 V90 H0Z" fill="var(--white)"/>
  </svg>
</section>

<section class="welcome">
  <h2>Welcome to <span>Crestway Travel</span></h2>
  <p class="lead">We provide airport transfers to and from all major UK airports, seaports, train station transfers and an executive business to business transfer service.</p>
  <div class="services">
    <div class="service">
      <div class="service-icon"><svg width="60" height="60" viewBox="0 0 60 60" fill="none" stroke="#fff" stroke-width="2.5" stroke-linejoin="round"><path d="M30 6c3 0 4 4 4 8v10l20 12v5l-20-6v10l6 5v4l-10-3-10 3v-4l6-5V35L6 41v-5l20-12V14c0-4 1-8 4-8z"/></svg></div>
      <h3>Airport Transfers</h3>
      <p>Lorem ipsum dolor sit amet, consectetur adipiscing elit do eiusmod tempor.</p>
    </div>
    <div class="service">
      <div class="service-icon"><svg width="60" height="60" viewBox="0 0 60 60" fill="none" stroke="#fff" stroke-width="2.5" stroke-linejoin="round"><rect x="14" y="6" width="32" height="40" rx="7"/><path d="M14 28h32M20 14h20v10H20z"/><circle cx="21" cy="37" r="2.5"/><circle cx="39" cy="37" r="2.5"/><path d="M20 46l-6 9M40 46l6 9"/></svg></div>
      <h3>Train Station Transfers</h3>
      <p>Lorem ipsum dolor sit amet, consectetur adipiscing elit do eiusmod tempor.</p>
    </div>
    <div class="service">
      <div class="service-icon"><svg width="60" height="60" viewBox="0 0 60 60" fill="none" stroke="#fff" stroke-width="2.5" stroke-linejoin="round"><path d="M24 6h12v8M16 26V14h28v12M8 32l22-8 22 8-6 16H14z"/><path d="M30 24v24M6 54c4 0 6-2 8-2s4 2 8 2 6-2 8-2 4 2 8 2 6-2 8-2 4 2 8 2"/></svg></div>
      <h3>Seaport Transfers</h3>
      <p>Lorem ipsum dolor sit amet, consectetur adipiscing elit do eiusmod tempor.</p>
    </div>
    <div class="service">
      <div class="service-icon"><svg width="60" height="60" viewBox="0 0 60 60" fill="none" stroke="#fff" stroke-width="2.5" stroke-linejoin="round"><path d="M6 28C8 14 20 8 30 8s22 6 24 20c-4-3-8-3-12 0-4-3-8-3-12 0-4-3-8-3-12 0-4-3-8-3-12 0z"/><path d="M30 8v20M30 28l2 28M10 54h40"/></svg></div>
      <h3>Holiday Transfers</h3>
      <p>Lorem ipsum dolor sit amet, consectetur adipiscing elit do eiusmod tempor.</p>
    </div>
    <div class="service">
      <div class="service-icon"><svg width="60" height="60" viewBox="0 0 60 60" fill="none" stroke="#fff" stroke-width="2.5" stroke-linejoin="round"><rect x="6" y="16" width="48" height="34" rx="3"/><path d="M22 16v-6h16v6M6 30h48M26 27h8v6h-8z"/></svg></div>
      <h3>Business Pick up and Drop off.</h3>
      <p>Lorem ipsum dolor sit amet, consectetur adipiscing elit do eiusmod tempor.</p>
    </div>
  </div>
</section>

<section class="about">
  <div class="about-photo" role="img" aria-label="Photo of a couple loading luggage into a car boot, orange tinted"></div>
  <h2>About Us</h2>
  <div class="about-card">
    <h3>We've been in the transport industry for over 60 years</h3>
    <p>That's 60 years of history and business 'know how'. Being one of the very first car transporters in the area we have now changed our expertise to transporting people throughout the UK and Europe. Our fleet of SUVs, Cars and Transporters are all top of the range latest models, boasting leather interior, A/C front and rear, ample boot space which means our customers benefit from the very finest in luxury road travel.</p>
    <p>We will continue to invest in our fleet to ensure our drivers and customers benefit fully from all that modern information and technology has to offer, without losing that personal touch. We offer the very best services in our field. We never settle for second best, and always have your satisfaction as our top priority. It's who we are, and we are proud of it.</p>
  </div>
</section>

<section class="always">
  <h2>Always <span>Here for You</span></h2>
  <div class="copy">
    <p>We provide airport transfers to and from all major UK airports, seaports, train station transfers and an executive business to business transfer service. Whether you have an individual or group transfer request, our company-owned fleet offers a choice of options to suit your needs, from luxury saloons and SUV's to 9-seat luxury transporters.</p>
    <p>We provide a door-to-door convenience from your home, office or hotel straight to any destination of your choice. Pre-booked or last minute we aim to cover any transport requirement. Allports and train station service; All pickups from arrivals will of been briefed as to your exact pickup point, or your chauffeur will be waiting with a name board. We also track your arrival time, so you can relax safe in the knowledge we will be waiting for you whatever time your journey completes.</p>
  </div>
  <a class="btn always-btn" href="#">Learn More</a>
  <div class="app-ring"><div class="app-photo" role="img" aria-label="Illustration of a smartphone showing a taxi booking app over a yellow taxi"></div></div>
</section>

<section class="booking">
  <div class="booking-photo" role="img" aria-label="Photo of a hand hailing a taxi on a city street, orange tinted"></div>
  <h2>Book a Ride with Us</h2>
  <form class="booking-form">
    <div class="field">First Name</div>
    <div class="field">Last Name</div>
    <div class="field">Email</div>
    <div class="field">Phone</div>
    <div class="field">Date <svg width="14" height="14" viewBox="0 0 14 14" fill="none" stroke="#555" stroke-width="1.4"><rect x="1" y="2.5" width="12" height="10.5"/><path d="M1 6h12M4 1v3M10 1v3"/></svg></div>
    <div class="field">Time <svg width="14" height="14" viewBox="0 0 14 14" fill="none" stroke="#555" stroke-width="1.4"><circle cx="7" cy="7" r="5.5"/><path d="M7 4v3l2 1.5"/></svg></div>
  </form>
  <a class="btn booking-btn" href="#">Submit Now</a>
  <svg class="booking-wave" width="1200" height="130" viewBox="0 0 1200 130" preserveAspectRatio="none">
    <path d="M0 130 V90 Q600 -40 1200 90 V130Z" fill="var(--orange)"/>
  </svg>
</section>

<footer class="site-footer">
  <div class="footer-col" style="left:112px;width:230px">
    <h4>Contact Us</h4>
    <ul class="contact-list">
      <li><svg width="16" height="20" viewBox="0 0 16 20" fill="none" stroke="#fff" stroke-width="1.5"><path d="M8 19s6-7 6-11A6 6 0 0 0 2 8c0 4 6 11 6 11z"/><circle cx="8" cy="8" r="2.2"/></svg><span>12,Sed ut perspiciatis un om iste natus error...</span></li>
      <li><svg width="16" height="16" viewBox="0 0 16 16" fill="none" stroke="#fff" stroke-width="1.5"><path d="M3 1h3l1.5 4L5.5 6.5a9 9 0 0 0 4 4L11 8.5l4 1.5v3c0 1-1 2-2 2A13 13 0 0 1 1 3c0-1 1-2 2-2z"/></svg><span>Phone : 07700 900461</span></li>
      <li><svg width="18" height="14" viewBox="0 0 18 14" fill="none" stroke="#fff" stroke-width="1.5"><rect x="1" y="1" width="16" height="12"/><path d="M1 1l8 7 8-7"/></svg><span>info@crestwaytravel.co.uk</span></li>
    </ul>
  </div>
  <div class="footer-col" style="left:395px">
    <h4>Quick Links</h4>
    <ul class="link-list"><li>Home</li><li>Services</li><li>About Us</li><li>VIP</li><li>Contact us</li></ul>
  </div>
  <div class="footer-col" style="left:603px">
    <h4>Other Links</h4>
    <ul class="link-list"><li>Terms of service</li><li>Privacy policy</li><li>Blog</li><li>Map</li><li>FAQ</li></ul>
  </div>
  <div class="footer-col newsletter" style="left:803px">
    <h4>Stay Connected</h4>
    <p>Join our newsletter and find out more.</p>
    <div class="email-field">Enter Email</div>
    <div class="btn subscribe">Subscribe</div>
  </div>
  <div class="footer-bottom">
    <p class="copyright">© copyright 2018 Crestway Travel . | Privacy policy</p>
    <div class="socials"><span></span><span></span></div>
  </div>
</footer>

</body>
</html>
```